Business Card Design

New business card design

Target Market(s)

Residential & Commercial Property Managers

Industry/Entity Type

Plumbing Services

Contact Information for Business Card

Name - Rowan Keddle, title - Director, Phone Number - 0431 286 517, email - rowan@tbk-plumbing.com.au, Company ABN - 73 215 904 386,

Font styles to use
Sans Serif

Colors
0054AA
0677BA
7BADD7
CADEEF
E8F1F8

```html
<!DOCTYPE html>
<html lang="en">
<head>
<meta charset="utf-8">
<title>tbk plumbing services – business card</title>
<link href="https://fonts.googleapis.com/css2?family=Fira+Sans+Condensed:wght@300;400;600&display=swap" rel="stylesheet">
<style>
  :root {
    --ink: #25292e;
    --grey-text: #5a5550;
    --blue-bright: #1a9fe0;
    --card: #ffffff;
    --drop-light: #f4f6f8;
    --drop-mid: #dfe3e7;
    --stage: #e6e8eb;
  }
  * { box-sizing: border-box; margin: 0; padding: 0; }
  html, body { width: 1200px; height: 675px; overflow: hidden; }
  body {
    background: var(--stage);
    font-family: "Fira Sans Condensed", "Arial Narrow", sans-serif;
    display: flex;
    align-items: center;
    justify-content: center;
    gap: 40px;
  }
  .card {
    position: relative;
    width: 520px;
    height: 297px;
    background: var(--card);
    box-shadow: 0 6px 18px rgba(40, 50, 60, 0.18);
    overflow: hidden;
  }
  .card-front .texture {
    position: absolute;
    inset: 0;
    background: radial-gradient(ellipse at 40% 40%, var(--drop-light), var(--drop-mid));
  }
  .brand-name {
    position: absolute;
    left: 0; right: 0;
    text-align: center;
    color: var(--ink);
    font-weight: 400;
    line-height: 1;
    white-space: nowrap;
  }
  .card-front .brand-name { top: 128px; font-size: 40px; }
  .card-back .brand-name { top: 58px; font-size: 34px; }
  .details {
    position: absolute;
    top: 150px;
    left: 0; right: 0;
    display: flex;
    justify-content: center;
    gap: 14px;
  }
  .person { text-align right; text-align: right; padding-top: 22px; }
  .person-name { color: var(--blue-bright); font-weight: 600; font-size: 25px; line-height: 1.1; }
  .person-title { color: var(--ink); font-size: 13px; letter-spacing: 0.5px; }
  .divider { width: 1px; background: var(--ink); height: 74px; }
  .contacts { list-style: none; font-size: 13px; color: var(--grey-text); display: flex; flex-direction: column; gap: 6px; padding-top: 2px; }
  .contacts li { display: flex; align-items: center; gap: 6px; }
  .contacts li:first-child { font-size: 15px; letter-spacing: 1px; }
  .contacts svg { width: 11px; height: 11px; fill: var(--blue-bright); flex: none; }
  .abn { position: absolute; top: 248px; left: 0; right: 0; text-align: center; font-size: 16px; color: var(--grey-text); }
  .abn-label { color: var(--blue-bright); }
</style>
</head>
<body>
  <section class="card card-front">
    <div class="texture" role="img" aria-label="Background pattern of water droplets on a white surface"></div>
    <p class="brand-name">tbk plumbing services</p>
  </section>

  <section class="card card-back">
    <p class="brand-name">tbk plumbing services</p>
    <div class="details">
      <div class="person">
        <div class="person-name">Rowan Keddle</div>
        <div class="person-title">Director</div>
      </div>
      <div class="divider"></div>
      <ul class="contacts">
        <li><svg viewBox="0 0 24 24"><path d="M6.6 10.8a15.1 15.1 0 0 0 6.6 6.6l2.2-2.2a1 1 0 0 1 1-.25 11.4 11.4 0 0 0 3.6.57 1 1 0 0 1 1 1V20a1 1 0 0 1-1 1A17 17 0 0 1 3 4a1 1 0 0 1 1-1h3.5a1 1 0 0 1 1 1c0 1.25.2 2.45.57 3.57a1 1 0 0 1-.25 1z"/></svg>0431 286 517</li>
        <li><svg viewBox="0 0 24 24"><path d="M2 5h20v14H2z"/><path d="M2 5l10 8 10-8v2l-10 8L2 7z" fill="#fff"/></svg>rowan@tbk-plumbing.com.au</li>
        <li><svg viewBox="0 0 24 24"><path d="M12 2a10 10 0 1 0 0 20 10 10 0 0 0 0-20zm6.9 6h-3a15.6 15.6 0 0 0-1.4-3.6A8 8 0 0 1 18.9 8zM12 4a14 14 0 0 1 1.9 4h-3.8A14 14 0 0 1 12 4zM4.3 14a8.2 8.2 0 0 1 0-4h3.4a16.5 16.5 0 0 0 0 4zm.8 2h3a15.6 15.6 0 0 0 1.4 3.6A8 8 0 0 1 5.1 16zm3-8h-3a8 8 0 0 1 4.4-3.6A15.6 15.6 0 0 0 8.1 8zM12 20a14 14 0 0 1-1.9-4h3.8A14 14 0 0 1 12 20zm2.3-6H9.7a14.7 14.7 0 0 1 0-4h4.6a14.7 14.7 0 0 1 0 4zm.2 5.6a15.6 15.6 0 0 0 1.4-3.6h3a8 8 0 0 1-4.4 3.6zm1.8-5.6a16.5 16.5 0 0 0 0-4h3.4a8.2 8.2 0 0 1 0 4z"/></svg>tbk-plumbing.com.au</li>
      </ul>
    </div>
    <p class="abn"><span class="abn-label">ABN</span> - 73 215 904 386</p>
  </section>
</body>
</html>
```